A business card design for a dental office. We have Two doctors working here. We practice general de

I already have a logo designed for the office with the name and a slogan.
Now I need to create design for a business card using the same logo.
Details Needed on the front side of the card are :
Bernard K. Oswin, DDS
Gerald M Fenwick, DDS
418 Birch Lane
Portland, CT 00000
Phone : 555 019 4831
Fax : 555 019 4832
Website : WWW.BrightmoorToothHaven.Com
Office hours by appointment
On the back side of the card need :
Appointment
Date....................Time...................
With....................................
If unable to keep your appointment, please give 24-48 hours notice in order to avoid broken appointment fee.

Industry/Entity Type

Dental Clinic

Contact Information for Business Card

Bernard K. Oswin, DDS
Gerald M Fenwick, DDS
418 Birch Lane
Portland, CT 00000
Phone : 555 019 4831
Fax : 555 019 4832
Appointment

Requirements
Must have
• Keep the Name and slogan on the logo on the front of the card. You can move them around the Logo and Name/Slogan of business (Oswin Family Dentistry/We give you reasons to smile) as you wish to get a feel of the design.
• Bernard K. Oswin, DDS
• Gerald M Fenwick, DDS
• 418 Birch Lane
• Portland, CT 00000
• Phone : 555 019 4831
• Fax : 555 019 4832
• WWW.BrightmoorToothHaven.Com
• Keep these three groups above as they are together now in different areas of the front side.
• On the back side of the card need :
• Appointment
• Date....................Time...................
• With....................................
• If unable to keep your appointment, please give 24-48 hours notice in order to avoid broken appointment fee.

```html
<!DOCTYPE html>
<html lang="en">
<head>
<meta charset="utf-8">
<title>Oswin Family Dentistry – Business Card</title>
<link rel="stylesheet" href="https://fonts.googleapis.com/css2?family=Source+Sans+3:ital,wght@0,400;0,600;0,700;1,700&display=swap">
<style>
  :root {
    --page-bg: #e9e6e1;
    --card-white: #ffffff;
    --card-grey: #dcdde0;
    --brand-blue: #1f5fa8;
    --deep-blue: #1a5c9e;
    --mid-blue: #3a82c2;
    --soft-blue: #6fa8d8;
    --bridge-teal: #2aa88e;
    --rule-grey: #b9bcc2;
    --text-grey: #4a4d52;
    --sail-grey: #dfe6ee;
  }
  * { margin: 0; padding: 0; box-sizing: border-box; }
  html, body { width: 1200px; height: 843px; overflow: hidden; }
  body {
    background: var(--page-bg);
    font-family: "Source Sans 3", "Myriad Pro", sans-serif;
    position: relative;
  }
  .card {
    position: absolute;
    left: 280px;
    width: 640px;
    height: 366px;
    border-radius: 22px;
    overflow: hidden;
    box-shadow: 0 6px 18px rgba(0,0,0,0.22);
  }

  /* Back side – appointment card */
  .card-back {
    top: 36px;
    background: linear-gradient(180deg, var(--card-white) 0%, var(--card-white) 55%, var(--card-grey) 100%);
  }
  .brand {
    position: absolute;
    top: 34px;
    right: 40px;
    display: flex;
    align-items: center;
    gap: 12px;
  }
  .brand-mark {
    width: 56px; height: 56px;
    border-radius: 50%;
    background: var(--bridge-teal);
  }
  .brand-name {
    font-weight: 700;
    font-size: 22px;
    letter-spacing: 0.5px;
    text-transform: uppercase;
    color: var(--brand-blue);
  }
  .appt-title {
    position: absolute;
    top: 118px; left: 44px;
    font-weight: 700;
    font-size: 28px;
    color: var(--brand-blue);
  }
  .appt-row {
    position: absolute;
    left: 44px;
    right: 44px;
    display: flex;
    align-items: flex-end;
    gap: 10px;
    font-size: 22px;
    color: var(--brand-blue);
  }
  .appt-row .rule { flex: 1; border-bottom: 1.5px solid var(--rule-grey); height: 1px; margin-bottom: 6px; }
  .row-date { top: 176px; }
  .row-with { top: 232px; }
  .appt-note {
    position: absolute;
    left: 44px; right: 44px; top: 286px;
    text-align: center;
    font-size: 17px;
    line-height: 1.35;
    color: var(--text-grey);
  }

  /* Front side – contact card */
  .card-front {
    top: 440px;
    background: linear-gradient(180deg,
      var(--card-white) 0%, var(--card-white) 41%,
      var(--soft-blue) 42%, var(--mid-blue) 55%, var(--deep-blue) 100%);
  }
  .bridge-art {
    position: absolute;
    left: 0; top: 0;
    width: 640px; height: 152px;
  }
  .contact {
    position: absolute;
    left: 44px;
    top: 170px;
    color: var(--card-white);
    text-shadow: 0 1px 2px rgba(10,40,80,0.35);
  }
  .doctor {
    font-weight: 600;
    font-size: 26px;
    line-height: 1.1;
  }
  .doctor small { font-size: 19px; font-weight: 600; }
  .address {
    margin-top: 6px;
    font-size: 18px;
    line-height: 1.3;
  }
  .address b { font-weight: 700; }
  .hours {
    font-weight: 700;
    font-style: italic;
    font-size: 20px;
    margin-top: 4px;
  }
  .sail-art {
    position: absolute;
    right: 40px;
    bottom: 30px;
    width: 40px; height: 46px;
  }
</style>
</head>
<body>

  <section class="card card-back" aria-label="Appointment card, back side">
    <div class="brand">
      <span class="brand-mark" aria-hidden="true"></span>
      <span class="brand-name">Oswin Family Dentistry</span>
    </div>
    <h2 class="appt-title">Appointment</h2>
    <div class="appt-row row-date">
      <span>Date:</span><span class="rule"></span>
      <span>Time:</span><span class="rule"></span>
    </div>
    <div class="appt-row row-with">
      <span>With:</span><span class="rule"></span>
    </div>
    <p class="appt-note">If unable to keep your appointment, please give 24-48 hours notice<br>in order to avoid broken appointment fee.</p>
  </section>

  <section class="card card-front" aria-label="Business card, front side">
    <svg class="bridge-art" role="img" aria-label="Illustration of a teal arched truss bridge over water" viewBox="0 0 640 152">
      <defs>
        <linearGradient id="bridgeTone" x1="0" y1="0" x2="0" y2="1">
          <stop offset="0" stop-color="#bfe8dc"/>
          <stop offset="1" stop-color="#e6f4f0"/>
        </linearGradient>
      </defs>
      <rect x="0" y="0" width="640" height="152" fill="url(#bridgeTone)"/>
    </svg>
    <div class="contact">
      <p class="doctor">Bernard K. Oswin, <small>DDS</small></p>
      <p class="doctor">Gerald M Fenwick, <small>DDS</small></p>
      <p class="address">418 Birch Lane, Portland, CT 00000<br><b>P:</b> 555 019 4831 &nbsp;<b>F:</b> 555 019 4832 &nbsp;<b>W:</b> BrightmoorToothHaven.Com</p>
      <p class="hours">Office hours by appointment</p>
    </div>
    <svg class="sail-art" role="img" aria-label="Small sailboat motif" viewBox="0 0 40 46">
      <rect x="0" y="0" width="40" height="46" rx="4" fill="var(--sail-grey)" opacity="0.6"/>
    </svg>
  </section>

</body>
</html>
```